Redesign of business card for Cedar Ridge Mechanical

We are looking for a new design for our business cards for Cedar Ridge Mechanical. We are a plumbing & HVAC construction company, operating on the West Coast of Canada and USA. Logo attached.
Industry/Entity Type
Construction - Plumbing & HVAC
Contact Information for Business Card
Name, address, phone numbers, email, website address
Look and feel
Each slider illustrates characteristics of the customer's brand and the style your logo design should communicate.

```html
<!DOCTYPE html>
<html lang="en">
<head>
<meta charset="utf-8">
<title>Cedar Ridge Mechanical – Business Card</title>
<link rel="stylesheet" href="https://fonts.googleapis.com/css2?family=Montserrat:wght@400;500;700&display=swap">
<style>
  :root {
    --stage: #3b3c41;
    --ink: #0d0d0d;
    --paper: #ffffff;
    --grey: #8c8c8c;
    --back-card: #161616;
    --back-mark: #2e2e2e;
  }
  * { box-sizing: border-box; margin: 0; padding: 0; }
  html, body { width: 1200px; height: 913px; overflow: hidden; }
  body {
    background: var(--stage);
    font-family: "Montserrat", Arial, sans-serif;
    position: relative;
  }
  .card {
    position: absolute;
    width: 560px;
    height: 320px;
    border-radius: 20px;
    overflow: hidden;
  }
  .card-back {
    left: 80px; top: 90px;
    background: var(--back-card);
    display: flex; align-items: center; justify-content: center; gap: 14px;
  }
  .card-front { left: 560px; top: 480px; background: var(--paper); }
  .brand { display: flex; align-items: center; gap: 12px; }
  .brand-square { width: 26px; height: 26px; }
  .brand-name {
    font-weight: 700; text-transform: uppercase; letter-spacing: 1px;
  }
  .card-back .brand-square { background: var(--back-mark); width: 34px; height: 34px; }
  .card-back .brand-name { color: var(--back-mark); font-size: 22px; }
  .card-front .brand { position: absolute; right: 28px; top: 40px; }
  .card-front .brand-square { background: var(--ink); }
  .card-front .brand-name { color: var(--ink); font-size: 15px; }
  .wave { position: absolute; inset: 0; }
  .name-tab {
    position: absolute; left: 0; top: 106px; width: 16px; height: 46px; background: var(--ink);
  }
  .person { position: absolute; left: 30px; top: 104px; color: var(--ink); }
  .person-name { font-size: 23px; font-weight: 700; letter-spacing: 0.5px; }
  .person-role { font-size: 15px; font-weight: 400; margin-top: 2px; }
  .contact { position: absolute; left: 28px; top: 196px; color: var(--paper); font-size: 14.5px; }
  .address { line-height: 21px; margin-bottom: 10px; padding-left: 22px; }
  .contact-line { display: flex; align-items: center; gap: 8px; height: 22px; }
  .contact-line svg { width: 14px; height: 14px; flex: none; }
</style>
</head>
<body>
  <section class="card card-back" aria-label="Card back">
    <div class="brand">
      <span class="brand-square"></span>
      <span class="brand-name">Cedar Ridge Mechanical</span>
    </div>
  </section>

  <section class="card card-front" aria-label="Card front">
    <svg class="wave" viewBox="0 0 560 320" preserveAspectRatio="none" aria-hidden="true">
      <path d="M150,178 C260,130 380,112 470,110 C510,109 540,104 560,96 L560,122 C520,130 470,128 400,128 C300,130 220,150 150,178 Z" fill="#8c8c8c"/>
      <path d="M0,160 C90,205 200,170 320,138 C420,112 500,118 560,132 L560,320 L0,320 Z" fill="#0d0d0d"/>
      <path d="M60,200 C170,190 260,150 380,135 C300,150 200,185 60,200 Z" fill="#ffffff"/>
    </svg>

    <div class="brand">
      <span class="brand-square"></span>
      <span class="brand-name">Cedar Ridge Mechanical</span>
    </div>

    <span class="name-tab"></span>
    <div class="person">
      <div class="person-name">DANIEL HAYES</div>
      <div class="person-role">Managing Director</div>
    </div>

    <div class="contact">
      <div class="address">Your address, City<br>State, Zip 1234</div>
      <div class="contact-line">
        <svg viewBox="0 0 16 16"><path d="M4 1.5 6.3 4 5 5.8c.8 1.9 2.3 3.4 4.2 4.2L11 8.7l2.5 2.3-1.3 2.5C7 13.5 2.5 9 2.5 3.8Z" fill="#fff"/></svg>
        <span>123 456 789</span>
      </div>
      <div class="contact-line">
        <svg viewBox="0 0 16 16"><rect x="1.5" y="3.5" width="13" height="9" rx="1" fill="none" stroke="#fff" stroke-width="1.5"/><path d="M2 4.5 8 9l6-4.5" fill="none" stroke="#fff" stroke-width="1.5"/></svg>
        <span>info@youremail.com</span>
      </div>
      <div class="contact-line">
        <svg viewBox="0 0 16 16"><circle cx="8" cy="8" r="6.3" fill="none" stroke="#fff" stroke-width="1.4"/><path d="M1.7 8h12.6M8 1.7c-3 3.5-3 9.1 0 12.6M8 1.7c3 3.5 3 9.1 0 12.6" fill="none" stroke="#fff" stroke-width="1.1"/></svg>
        <span>www.yourwebsite.com</span>
      </div>
    </div>
  </section>
</body>
</html>
```